Step and Repeat Backdrop for wedding reception photo booth

Would like to have a Step and Repeat Backdrop (8 foot high by 10 foot wide) that incorporates the wedding logo (attached) and the names Helen and Gavin. Background should be white, and wedding colors are burgundy and gold. Show me creativity :-) I have included some random samples.

```html
<!DOCTYPE html>
<html lang="en">
<head>
<meta charset="utf-8">
<title>Helen &amp; Gavin — Step and Repeat Backdrop</title>
<link href="https://fonts.googleapis.com/css2?family=Playfair+Display:wght@500;600&display=swap" rel="stylesheet">
<style>
  :root {
    --stage: #e4e4e7;
    --backdrop: #ffffff;
    --gold: #d69a2a;
    --gold-deep: #b8692a;
    --gold-light: #f3c63a;
    --burgundy: #8b1237;
    --ink-light: #ffffff;
  }
  html, body {
    margin: 0;
    padding: 0;
    width: 1200px;
    height: 1200px;
    overflow: hidden;
    background: var(--stage);
  }
  .canvas {
    position: relative;
    width: 1200px;
    height: 1200px;
  }
  .backdrop {
    position: absolute;
    left: 0;
    top: 115px;
    width: 1200px;
    height: 971px;
    background: var(--backdrop);
  }
  .backdrop svg {
    display: block;
    width: 100%;
    height: 100%;
  }
  .repeat-mark {
    font-family: "Playfair Display", Georgia, serif;
    font-weight: 600;
    font-size: 50px;
    fill: var(--gold);
  }
  .emblem-monogram {
    font-family: "Playfair Display", Georgia, serif;
    font-weight: 600;
    font-size: 215px;
    fill: var(--gold);
  }
  .name-band { fill: var(--burgundy); }
  .band-names {
    font-family: "Playfair Display", Georgia, serif;
    font-weight: 500;
    font-size: 32px;
    letter-spacing: 14px;
    fill: var(--ink-light);
  }
  .band-ring {
    fill: none;
    stroke: var(--ink-light);
    stroke-width: 2.5;
  }
  .emblem-frame {
    fill: none;
    stroke: url(#frameGold);
    stroke-width: 7;
    stroke-linejoin: miter;
  }
  .ornament-area { fill: url(#ornamentGold); }
</style>
</head>
<body>
<main class="canvas">
  <section class="backdrop" aria-label="Step and repeat backdrop for Helen and Gavin">
    <svg viewBox="0 0 1337 1082" xmlns="http://www.w3.org/2000/svg">
      <defs>
        <linearGradient id="frameGold" x1="0" y1="0" x2="1" y2="0">
          <stop offset="0" stop-color="var(--gold-deep)"/>
          <stop offset="1" stop-color="var(--gold-light)"/>
        </linearGradient>
        <linearGradient id="ornamentGold" x1="0" y1="0" x2="1" y2="0">
          <stop offset="0" stop-color="#c98a35" stop-opacity="0.35"/>
          <stop offset="1" stop-color="#f0c040" stop-opacity="0.35"/>
        </linearGradient>
      </defs>

      <g class="repeat-pattern" text-anchor="middle">
        <!-- row 1 -->
        <text class="repeat-mark" x="83" y="108">H&amp;G</text>
        <text class="repeat-mark" x="316" y="108">H&amp;G</text>
        <text class="repeat-mark" x="549" y="108">H&amp;G</text>
        <text class="repeat-mark" x="782" y="108">H&amp;G</text>
        <text class="repeat-mark" x="1015" y="108">H&amp;G</text>
        <text class="repeat-mark" x="1248" y="108">H&amp;G</text>
        <!-- row 2 -->
        <text class="repeat-mark" x="83" y="288">H&amp;G</text>
        <text class="repeat-mark" x="316" y="288">H&amp;G</text>
        <text class="repeat-mark" x="1015" y="288">H&amp;G</text>
        <text class="repeat-mark" x="1248" y="288">H&amp;G</text>
        <!-- rows 3 to 5 -->
        <text class="repeat-mark" x="83" y="468">H&amp;G</text>
        <text class="repeat-mark" x="1248" y="468">H&amp;G</text>
        <text class="repeat-mark" x="83" y="648">H&amp;G</text>
        <text class="repeat-mark" x="1248" y="648">H&amp;G</text>
        <text class="repeat-mark" x="83" y="828">H&amp;G</text>
        <text class="repeat-mark" x="1248" y="828">H&amp;G</text>
        <!-- row 6 -->
        <text class="repeat-mark" x="83" y="1008">H&amp;G</text>
        <text class="repeat-mark" x="316" y="1008">H&amp;G</text>
        <text class="repeat-mark" x="549" y="1008">H&amp;G</text>
        <text class="repeat-mark" x="782" y="1008">H&amp;G</text>
        <text class="repeat-mark" x="1015" y="1008">H&amp;G</text>
        <text class="repeat-mark" x="1248" y="1008">H&amp;G</text>
      </g>

      <g class="emblem">
        <polygon class="emblem-frame" points="522,191 810,191 1015,397 1015,685 810,891 522,891 316,685 316,397"/>
        <polygon class="emblem-frame" points="657,162 928,265 1042,530 932,795 674,920 402,815 287,545 392,277"/>

        <rect class="ornament-area" x="447" y="270" width="440" height="130" rx="60" role="img" aria-label="Gold scroll flourish with fleur-de-lis above the monogram"/>
        <rect class="ornament-area" x="447" y="592" width="440" height="132" rx="60" role="img" aria-label="Gold scroll flourish with fleur-de-lis below the monogram"/>
        <rect class="ornament-area" x="257" y="572" width="180" height="272" rx="80" role="img" aria-label="Gold floral spray of leaves and blossoms, left"/>
        <rect class="ornament-area" x="894" y="572" width="174" height="272" rx="80" role="img" aria-label="Gold floral spray of leaves and blossoms, right"/>

        <text class="emblem-monogram" x="667" y="572" text-anchor="middle">H&amp;G</text>

        <rect class="name-band" x="427" y="747" width="470" height="84"/>
        <text class="band-names" x="638" y="803" text-anchor="end">Helen</text>
        <circle class="band-ring" cx="672" cy="793" r="15"/>
        <text class="band-names" x="710" y="803" text-anchor="start">Gavin</text>
      </g>
    </svg>
  </section>
</main>
</body>
</html>
```